WP website design for Kemble

We need a wordpress design that will incorporate a professional color scheme with company logo in a clean layout. The design needs to consider that this will be developed on a responsive theme. Colors are will be the green of the logo and any others that will creatively highlight it.

Industry/Entity Type

It Company

Font styles to use
Sans Serif

Requirements
Must have
• Navigation: 1) Home 2) Auctions 3) Auction Services 4) Sellers 5) TR Kemble Livestock 6) About Us 7) Contact Us
Site will have slideshow element, image attached.
Widgets will be: 1)Email Signup form 2) Featured Auctions widget 3) Social Media (FB, video channel, RSS) 4) News & Events blog
Footer will have smaller company logo, association logos (attached) and contact info (below)
▪ T.R. Kemble Inc. / Auctioneers
▪ 4710 NC Hwy 91
▪ Brookhaven, NC 27999
▪ Office: (555) 318-6402
▪ Cell: (555) 274-8813
▪ email: trkemble@trkemble-example.com
Nice to have
• Site will have drop-down menus - please indicate the styling, for instance the dropdown menus

```html
<!DOCTYPE html>
<html lang="en">
<head>
<meta charset="utf-8">
<title>T.R. Kemble Inc. / Auctioneers</title>
<link href="https://fonts.googleapis.com/css2?family=Satisfy&family=Ubuntu:wght@400;500;700&display=swap" rel="stylesheet">
<style>
:root{
  --green:#3a8a1c;
  --green-dark:#2e7414;
  --green-light:#4fa52a;
  --yellow:#f2e01a;
  --yellow-soft:#f5e83a;
  --card-bg:#ececec;
  --text:#333;
  --red:#d61a1a;
  --white:#fff;
}
*{box-sizing:border-box;margin:0;padding:0}
html,body{width:1001px;height:1200px;overflow:hidden}
body{position:relative;background:var(--white);font-family:"Ubuntu",sans-serif;color:var(--text)}
.abs{position:absolute}
.header{left:0;top:0;width:1001px;height:334px;background:linear-gradient(#fff 40px,#f4f4f4 120px,#dedede)}
.navbar{left:0;top:0;width:1001px;height:42px;background:var(--green)}
.nav{left:336px;top:0;height:42px;display:flex;list-style:none}
.nav li{height:42px;line-height:40px;padding:0 12px;color:var(--white);font-size:12.5px;font-weight:500}
.nav li.active{background:var(--green-light);color:var(--yellow)}
.dropdown{left:392px;top:42px;width:131px;background:var(--green-light);padding-bottom:12px;z-index:5}
.dropdown div{height:27px;line-height:27px;padding-left:13px;font-size:11px;font-weight:700;color:var(--white)}
.dropdown div.on{background:var(--yellow);color:var(--text)}
.logo{left:87px;top:-101px;width:234px;height:234px;border-radius:50%;background:var(--yellow);border:3px solid #fff;box-shadow:0 2px 4px rgba(0,0,0,.25);display:flex;flex-direction:column;align-items:center;justify-content:flex-end;padding-bottom:28px}
.logo span{font-weight:700;color:var(--green);font-size:22px;line-height:1.15}
.script{font-family:"Satisfy",cursive}
.side-script{left:128px;top:176px;font-size:25px;color:var(--green)}
.social{top:238px;width:46px;height:46px;border-radius:50%;border:3px solid #ccc;box-shadow:0 1px 3px rgba(0,0,0,.3)}
.social.s1{left:115px;background:#3b5fa8}
.social.s2{left:177px;background:#d82a25}
.social.s3{left:241px;background:#f07a26}
.slide{left:344px;top:48px;width:569px;height:266px;background:linear-gradient(#b9d3e6 0%,#c9a47a 42%,#d8a04c 55%,#a07a4a 70%,#8a6a45 100%)}
.dots{left:575px;top:285px;display:flex;gap:9px}
.dots i{display:block;width:15px;height:15px;border-radius:50%;background:#222}
.dots i.on{background:var(--yellow)}
.welcome{left:89px;top:366px;font-size:28px;font-weight:400;color:var(--green)}
.intro{left:93px;top:412px;width:520px;font-size:12px;line-height:17px}
.card{left:96px;width:505px;background:var(--card-bg);border:1px solid #c8c8c8}
.card-head{height:37px;background:linear-gradient(var(--green-light),var(--green-dark));color:var(--white);font-size:16px;line-height:37px;padding-left:17px}
.photo{left:9px;width:267px;box-shadow:0 2px 3px rgba(0,0,0,.4)}
.info{left:289px;width:210px;font-size:11px;line-height:16px;color:#555}
.info .title{color:var(--red);text-align:center;font-size:11.5px;font-weight:500;line-height:14px}
.info .center{text-align:center;font-weight:500;line-height:14px}
.info b{color:#333}
.info .kind{font-weight:700;color:#333}
.btn{height:28px;border-radius:4px;background:linear-gradient(#555,#2c2c2c);color:var(--white);font-size:11.5px;line-height:28px;display:flex;align-items:center;gap:6px;padding-left:11px;box-shadow:0 2px 2px rgba(0,0,0,.35)}
.bid{left:289px;width:190px;height:31px;border:1px solid #999;border-radius:4px;background:#fff;font-weight:700;font-size:12.5px;color:#1d4e8a;display:flex;align-items:center;gap:7px;padding-left:10px;box-shadow:0 2px 3px rgba(0,0,0,.35)}
.sidebar{left:650px;top:358px;width:263px;height:649px;background:var(--green);color:var(--white)}
.sidebar .h{position:absolute;left:23px;font-size:24px}
.sidebar p{position:absolute;font-size:11.5px;line-height:17px}
.email-input{left:24px;top:96px;width:190px;height:29px;background:#fff;color:#777;font-size:11px;line-height:29px;padding-left:10px}
.subscribe{left:26px;top:142px;width:91px;height:27px;background:linear-gradient(var(--yellow-soft),#d8c40d);border:1px solid #6a6a00;color:#222;font-size:13px;font-weight:700;line-height:25px;text-align:center}
.divider{left:18px;width:227px;height:1px;background:rgba(255,255,255,.3)}
.feature-img{left:52px;top:289px;width:148px;height:89px;border:2px solid var(--green-light);background:linear-gradient(#c3d8e8,#9ab27e 55%,#6f8f4e)}
.news{left:20px;top:527px;width:230px;list-style:none;font-size:11px;line-height:13px}
.news li{margin-bottom:10px;padding-left:10px;position:relative}
.news li:before{content:"";position:absolute;left:0;top:5px;width:4px;height:4px;border-radius:50%;background:#fff}
.footer{left:0;top:1042px;width:1001px;height:127px;background:var(--green);color:var(--white)}
.contact{left:103px;top:24px;font-family:Arial,sans-serif;font-size:11.7px;line-height:16.7px;font-style:normal}
.foot-logo{left:430px;top:22px;width:130px;text-align:center;font-weight:700;font-size:18px;line-height:22px}
.badge{top:32px;height:58px;border:2px solid rgba(255,255,255,.85)}
.copyright{left:0;top:1169px;width:1001px;height:31px;background:var(--yellow);text-align:center;font-family:Arial,sans-serif;font-size:10.5px;line-height:31px;color:#333}
</style>
</head>
<body>
<header class="abs header"></header>
<div class="abs navbar"></div>
<ul class="abs nav">
  <li>Home</li><li class="active">Auctions</li><li>Auction Services</li><li>Sellers</li><li>TR Kemble Livestock</li><li>About Us</li><li>Contact Us</li>
</ul>
<div class="abs logo"><span>T.R. Kemble</span><span>Auctioneers</span></div>
<div class="abs side-script script">Email Signup</div>
<div class="abs social s1" role="img" aria-label="Social page link"></div>
<div class="abs social s2" role="img" aria-label="Video channel link"></div>
<div class="abs social s3" role="img" aria-label="News feed link"></div>
<div class="abs slide" role="img" aria-label="Slideshow photo of a pond reflecting autumn trees and golden grass"></div>
<div class="abs dots"><i></i><i class="on"></i><i></i><i></i><i></i></div>
<div class="abs dropdown"><div>Upcoming Auction</div><div class="on">Past Auction</div></div>

<h1 class="abs welcome script">Welcome to T.R Kemble</h1>
<p class="abs intro">Our auction business was started in 1977. We conduct farm equipment, logging &amp; industrial equipment, real estate, antique &amp; cattle sales.</p>

<section class="abs card" style="top:467px;height:258px">
  <div class="card-head">CATTLE &amp; FARM EQUIPMENT AUCTION</div>
  <div class="abs photo" style="top:41px;height:162px;background:linear-gradient(#bcd6ea,#9c5a45 45%,#7c8a55 62%,#6a9a3e)" role="img" aria-label="Red brick ranch home with front lawn"></div>
  <div class="abs info" style="top:46px">
    <div class="title">3 BR / 1+ BA BRICK HOME &amp; 0.627 ACRE LOT</div>
    <div class="center" style="margin-top:6px">DANA WHITLOW - DALTON COUNTY CLERK &amp; MASTER</div>
    <div class="center" style="margin-top:6px;font-size:10.5px">555-610-4472</div>
    <div class="kind" style="margin-top:12px">LIVE ON-SITE AUCTION</div>
    <div><b>Location:</b> <svg width="9" height="12" viewBox="0 0 9 12"><path d="M4.5 0A4.5 4.5 0 0 0 0 4.5C0 8 4.5 12 4.5 12S9 8 9 4.5A4.5 4.5 0 0 0 4.5 0z" fill="#d61a1a"/><circle cx="4.5" cy="4.5" r="1.6" fill="#fff"/></svg> 3140 Millbrook Road, (Dalton County), Millford, TN 38599</div>
    <div><b>Begins:</b>&nbsp; 09/20/14 at 10:00 AM CDT</div>
  </div>
  <div class="abs btn" style="left:59px;top:218px;width:80px"><svg width="14" height="14"><rect x="2" y="1" width="10" height="12" fill="#eee"/></svg>Details</div>
  <div class="abs btn" style="left:151px;top:218px;width:81px"><svg width="14" height="14"><rect x="1" y="3" width="12" height="9" fill="#f1c94a"/></svg>Photos</div>
</section>

<section class="abs card" style="top:736px;height:273px">
  <div class="card-head">CATTLE &amp; FARM EQUIPMENT AUCTION</div>
  <div class="abs photo" style="top:41px;height:178px;background:linear-gradient(#dfe8ef,#5a5a5a 35%,#7a4638 55%,#5f9a35 70%,#78ac44)" role="img" aria-label="Brick home with porch and green lawn"></div>
  <div class="abs info" style="top:46px">
    <div class="title">NICE 4 BEDROOM - 3½ BA BRICK HOME &amp; 10.73± ACRES (1 TRACT)</div>
  </div>
  <div class="abs bid" style="top:92px"><svg width="18" height="14"><rect x="1" y="1" width="16" height="10" fill="#4a86c5"/><rect x="6" y="11" width="6" height="2" fill="#777"/></svg>Click for Online Bidding</div>
  <div class="abs info" style="top:142px">
    <div class="kind">ONLINE BIDDING ONLY</div>
    <div><b>Property Location:</b> <svg width="9" height="12" viewBox="0 0 9 12"><path d="M4.5 0A4.5 4.5 0 0 0 0 4.5C0 8 4.5 12 4.5 12S9 8 9 4.5A4.5 4.5 0 0 0 4.5 0z" fill="#d61a1a"/><circle cx="4.5" cy="4.5" r="1.6" fill="#fff"/></svg> 1657 Cedar Run Trail, (Dalton County), Millford, TN 38599</div>
    <div><b>Began:</b>&nbsp; 08/29/14 at 5:00 PM CDT</div>
    <div><b>Ends:</b>&nbsp; 09/23/14 at 10:00 AM CDT</div>
  </div>
  <div class="abs btn" style="left:59px;top:233px;width:80px"><svg width="14" height="14"><rect x="2" y="1" width="10" height="12" fill="#eee"/></svg>Details</div>
  <div class="abs btn" style="left:151px;top:233px;width:81px"><svg width="14" height="14"><rect x="1" y="3" width="12" height="9" fill="#f1c94a"/></svg>Photos</div>
</section>

<aside class="abs sidebar">
  <div class="h script" style="top:18px">Email Signup</div>
  <p style="left:23px;top:55px;width:225px">Please join our free mailing list to get auction alerts for upcoming events.</p>
  <div class="abs email-input">Enter Your Email</div>
  <div class="abs subscribe">Subscribe</div>
  <div class="abs divider" style="top:190px"></div>
  <div class="h script" style="top:206px">Featured Auctions</div>
  <p style="left:0;top:250px;width:263px;text-align:center;font-size:10.5px;font-weight:500">13.35 ACRES OF PRIME DEVELOP<br>&amp; 33RD STREET</p>
  <div class="abs feature-img" role="img" aria-label="Crowd gathered in front of a white farmhouse"></div>
  <p style="left:0;top:390px;width:263px;text-align:center;font-size:10.5px;line-height:13.5px">LOTS 13 &amp; 14 FOR SALE, MARLOW<br>IOWA<br>Elm Street, Marlow, IA 52699</p>
  <div class="abs divider" style="top:463px"></div>
  <div class="h script" style="top:478px">News &amp; Events blog</div>
  <ul class="abs news">
    <li>Great Land Auction Companies Make all the Difference</li>
    <li>Great OK Farms for Sale at Auction Prices</li>
    <li>Farmland Auctions on Route 66</li>
    <li>Great Land Auction Companies Make all the Difference</li>
  </ul>
</aside>

<footer class="abs footer">
  <address class="abs contact">T.R. Kemble Inc. / Auctioneers<br>4710 NC Hwy 91<br>Brookhaven, NC 27999<br>Office: (555) 318-6402 , Cell: (555) 274-8813<br>Email: trkemble@trkemble-example.com</address>
  <div class="abs foot-logo">T.R. Kemble<br>Auctioneers</div>
  <div class="abs badge" style="left:598px;width:104px;border-radius:6px" role="img" aria-label="Auctioneers association badge"></div>
  <div class="abs badge" style="left:721px;width:76px;border-radius:10px" role="img" aria-label="Beef industry badge"></div>
  <div class="abs badge" style="left:820px;top:26px;width:76px;height:76px;border-radius:50%" role="img" aria-label="Cattle association badge"></div>
</footer>
<div class="abs copyright">Copyright © 2014 T.R. Kemble, Inc. / Auctioneers. All Rights Reserved.</div>
</body>
</html>
```